Federal IT Consulting Company - Brisolux Consulting Group

We're seeking a skilled web designer to create a modern, bold, and engaging WordPress website for Brisolux Consulting Group, LLC. Our company specializes in federal IT consulting, and our name is a play on "Brightening Solutions." The website should reflect our expertise in the federal technology marketplace and position us as a trusted partner for clients navigating their IT journey.

contact: info@brisoluxgrp-example.com

Current Status

WordPress is already installed on our hosting account
We have an existing logo (may need modernization)

Design Requirements

Style:

Modern and visually striking design
Bold elements to convey confidence and expertise
Incorporate the concept of "brightening solutions" into the design

Features:

Modern UX sliders for dynamic content presentation
Eye-catching, high-quality images (stock photos to be sourced by the designer)
Responsive design for all devices

Color Scheme:

To be proposed by the designer, should align with our brand and convey trust and technological expertise

Logo:

Evaluate our current logo
Create a transparent background version if needed
Propose modernization if deemed necessary

Accessibility:

Ensure design elements are accessible to users with disabilities
Use high contrast ratios for text and background colors
Provide text alternatives for non-text content

Website Structure
Create the following pages, with the possibility of subpages:

Home
Services
About
Contact

Specific Page Requirements
Home Page

Striking hero section with a clear value proposition
Overview of our services
Client testimonials or trust indicators

Services Page

Detailed list of our IT consulting services
Clear explanation of how we help navigate the federal IT landscape

About Page

Company history and mission
Team highlights (if applicable)
Our approach to federal IT consulting

Contact Page

Contact form
Other contact methods (phone, email)

Technical Requirements

Fully responsive design
SEO best practices implemented
Fast loading times
Integration with necessary plugins (to be discussed)
Training on how to update and maintain the site
Full compliance with Web Content Accessibility Guidelines (WCAG) 2.1 Level AA
Adherence to Section 508 standards for federal website accessibility
Implementation of necessary features for ADA compliance
Updates

Designs look the same

Target Market(s)

US Federal Govt customers looking for IT support.

Industry/Entity Type

IT Consulting

Coding

Coded - Design and coding required

Colors
0054AA
0677BA
7BADD7
CADEEF
E8F1F8
0094D4
00A9DD
6FCCEA
C7EBF8
E9F6FB
00AB8E
00BBA5
67D7C9
C6EFE9
E9F9F6

```html
<!DOCTYPE html>
<html lang="en">
<head>
<meta charset="utf-8">
<title>Brisolux Consulting Group – Federal IT Consulting</title>
<link href="https://fonts.googleapis.com/css2?family=Jost:wght@400;500;600&display=swap" rel="stylesheet">
<style>
:root{
  --navy:#0b2343;
  --navy-deep:#081b35;
  --blue:#0a66c2;
  --blue-btn:#0a7fd0;
  --cyan:#0e9ee0;
  --ink:#111820;
  --body:#3b4450;
  --light:#d6eaf8;
  --white:#ffffff;
  --star:#f5b623;
}
*{box-sizing:border-box;margin:0;padding:0}
html,body{width:1200px;height:3883px;overflow:hidden}
body{font-family:"Jost",sans-serif;color:var(--ink);background:var(--white);position:relative}
.abs{position:absolute}
.tag{position:absolute;font-size:12px;font-weight:500;letter-spacing:.6px;color:var(--blue);padding-left:8px;border-left:2px solid var(--blue);line-height:15px;text-transform:uppercase}
.tag.light{color:var(--white);border-color:var(--white)}
.h2{position:absolute;font-size:28px;font-weight:500;line-height:36px;color:var(--ink)}
.h2 em{font-style:normal;color:var(--cyan)}
.btn{position:absolute;display:flex;align-items:center;justify-content:center;font-size:14px;font-weight:500;border-radius:4px;color:var(--white);background:var(--blue-btn);box-shadow:0 6px 14px rgba(10,127,208,.25);white-space:nowrap}
.photo{position:absolute}

.header{position:absolute;left:0;top:0;width:1200px;height:70px;background:var(--white)}
.brand{position:absolute;display:flex;align-items:center;gap:10px;font-weight:600;letter-spacing:1px;text-transform:uppercase}
.brand .dot{border-radius:50%;border:4px solid var(--cyan)}
.nav{position:absolute;top:27px;font-size:14px;font-weight:500}
.hero{position:absolute;left:0;top:70px;width:1200px;height:488px;overflow:hidden}
.hero .photo{inset:0;background:linear-gradient(100deg,rgba(30,40,70,.85) 0%,rgba(40,45,70,.55) 38%,rgba(0,0,0,0) 60%),linear-gradient(180deg,#2e4770 0%,#7e6a75 35%,#c98e62 65%,#4a3a2a 100%)}
.hero h1{position:absolute;left:142px;top:126px;font-size:36px;font-weight:500;line-height:47px;color:var(--white);white-space:nowrap}
.hero p{position:absolute;left:142px;top:286px;font-size:15px;line-height:26px;color:var(--white);white-space:nowrap}
.btn.outline{background:transparent;border:1.5px solid rgba(255,255,255,.8);box-shadow:none}
.para{position:absolute;font-size:12.5px;line-height:22.6px;color:var(--body)}
.band{position:absolute;left:0;top:1432px;width:1200px;height:687px;background:var(--navy)}
.card{position:absolute;top:1256px;width:291px;height:262px;border-radius:8px;overflow:hidden}
.card .photo{inset:0}
.card .info{position:absolute;left:21px;width:249px;border:1px solid rgba(255,255,255,.85);border-radius:8px;background:rgba(20,30,50,.45);color:var(--white);padding:0 18px}
.card .title{font-size:15px;font-weight:500}
.card .desc{font-size:12px;line-height:19px;margin-top:8px;width:170px}
.card .go{position:absolute;right:18px;bottom:20px;width:26px;height:26px;border-radius:50%;background:var(--white);display:flex;align-items:center;justify-content:center}
.arrow-btn{position:absolute;width:36px;height:36px;border-radius:50%;display:flex;align-items:center;justify-content:center}
.quote-text{position:absolute;left:606px;top:1828px;width:430px;font-size:12.5px;line-height:22.6px;color:#dfe7f1}
.member{position:absolute;top:2318px;width:182px;text-align:center}
.member .photo{position:relative;width:182px;height:182px;border-radius:50%}
.member .name{margin-top:18px;font-size:15px;font-weight:600}
.member .role{font-size:11px;color:var(--cyan);margin-top:3px}
.socials{display:flex;justify-content:center;gap:10px;margin-top:12px}
.socials span{width:32px;height:32px;border-radius:50%;background:var(--blue-btn);display:flex;align-items:center;justify-content:center}
.socials span i{width:10px;height:10px;border-radius:50%;background:var(--white)}
.cta{position:absolute;left:142px;top:2730px;width:916px;height:328px;border-radius:60px 0 60px 0;overflow:hidden;background:linear-gradient(90deg,#0a6fc4 0%,#0d8fd6 55%,#3aa7dc 100%)}
.cta .photo{right:0;top:0;width:460px;height:328px;background:linear-gradient(180deg,#8fb7d8 0%,#c9d8e4 45%,#e8e4da 70%,#b88a45 100%);opacity:.9;-webkit-mask:linear-gradient(90deg,transparent 0,#000 35%);mask:linear-gradient(90deg,transparent 0,#000 35%)}
.cert{position:absolute;top:3286px;height:181px;box-shadow:0 6px 18px rgba(0,0,0,.12)}
.footer{position:absolute;left:0;top:3551px;width:1200px;height:332px;background:var(--navy-deep);color:var(--white)}
.fcol h4{font-size:15px;font-weight:500;color:var(--cyan);margin-bottom:14px}
.fcol a{display:block;font-size:12px;color:var(--white);text-decoration:none;margin-bottom:11px}
.fcol{position:absolute;top:82px}
.contact-row{display:flex;gap:12px;font-size:12px;line-height:17px;margin-bottom:14px}
</style>
</head>
<body>

<header class="header">
  <div class="brand" style="left:142px;top:17px;font-size:28px;color:var(--navy)"><span class="dot" style="width:36px;height:36px"></span>Brisolux</div>
  <nav>
    <span class="nav" style="left:695px;color:var(--cyan)">Home</span>
    <span class="nav" style="left:770px">About Us</span>
    <span class="nav" style="left:862px">Services</span>
  </nav>
  <div class="btn" style="left:950px;top:14px;width:108px;height:42px;font-size:13px">Contact Us</div>
</header>

<section class="hero">
  <div class="photo" role="img" aria-label="Capitol building dome at sunset with a flag on the left"></div>
  <div class="tag light" style="left:142px;top:100px">Welcome to Brisolux</div>
  <h1>Navigate Your Federal<br>IT Journey with<br>Confidence.</h1>
  <p>Expert Consulting Services to Guide Your<br>IT Strategy.</p>
  <div class="btn" style="left:142px;top:364px;width:170px;height:42px;background:var(--blue)">Explore Our Services</div>
  <div class="btn outline" style="left:326px;top:364px;width:190px;height:42px">Get A Free Consultation</div>
</section>

<section class="about">
  <div class="abs" style="left:142px;top:644px;width:81px;height:81px;border-radius:50%;background:var(--light)"></div>
  <div class="photo" role="img" aria-label="Capitol building under an evening sky" style="left:179px;top:681px;width:305px;height:325px;border-radius:10px;background:linear-gradient(180deg,#8aa0bd 0%,#d7b48c 45%,#a7a9ad 75%,#6c6f78 100%)"></div>
  <div class="photo" role="img" aria-label="Consultants working together at laptops" style="left:400px;top:879px;width:153px;height:145px;border-radius:8px;background:linear-gradient(135deg,#2a3a4e,#8a97a6 60%,#d8dde3);border:3px solid #fff"></div>
  <div class="tag" style="left:638px;top:690px">About Us</div>
  <div class="h2" style="left:638px;top:716px">Why Choose <em>Brisolux?</em></div>
  <p class="para" style="left:638px;top:775px;width:420px">There are many variations of passages of Lorem Ipsum available, but the majority have suffered alteration in some form, by injected humour, or randomised words which don't look even slightly believable. If you are going to use a passage of Lorem Ipsum, you need to be sure there isn't anything embarrassing hidden in the middle of text.</p>
  <p class="para" style="left:638px;top:904px;width:420px">It is a long established fact that a reader will be distracted by the readable content of a page when looking at its layout.</p>
  <div class="btn" style="left:639px;top:973px;width:111px;height:43px">Learn More</div>
</section>

<section class="services">
  <div class="band"></div>
  <div class="tag" style="left:142px;top:1109px">Popular Services</div>
  <div class="h2" style="left:142px;top:1136px">The Best Solution For<br>Your <em>Business</em></div>
  <div class="btn" style="left:957px;top:1164px;width:101px;height:42px">View All</div>

  <div class="card" style="left:142px">
    <div class="photo" role="img" aria-label="Security operations desk with multiple monitors" style="background:linear-gradient(160deg,#3a2a5a,#1d2d4a 50%,#0f1a2c)"></div>
    <div class="info" style="top:116px;height:125px;padding-top:18px">
      <div class="title">Cybersecurity</div>
      <div class="desc">There are many variations of passages of Lorem Ipsum available.</div>
      <div class="go"><svg width="10" height="10" viewBox="0 0 10 10"><path d="M2 8L8 2M3.5 2H8v4.5" stroke="#0a7fd0" stroke-width="1.4" fill="none"/></svg></div>
    </div>
  </div>
  <div class="card" style="left:454px">
    <div class="photo" role="img" aria-label="Hand touching a glowing cloud interface" style="background:linear-gradient(160deg,#1c3550,#2f6d95 50%,#0e2035)"></div>
    <div class="info" style="top:176px;height:65px;display:flex;align-items:center">
      <div class="title">Cloud Services</div>
      <div class="go" style="bottom:19px"><svg width="10" height="10" viewBox="0 0 10 10"><path d="M2 8L8 2M3.5 2H8v4.5" stroke="#0a7fd0" stroke-width="1.4" fill="none"/></svg></div>
    </div>
  </div>
  <div class="card" style="left:767px">
    <div class="photo" role="img" aria-label="Team meeting around laptops in a bright office" style="background:linear-gradient(160deg,#b78a4e,#6a6a5c 50%,#3b4552)"></div>
    <div class="info" style="top:176px;height:65px;display:flex;align-items:center">
      <div class="title">IT Strategy Consulting</div>
      <div class="go" style="bottom:19px"><svg width="10" height="10" viewBox="0 0 10 10"><path d="M2 8L8 2M3.5 2H8v4.5" stroke="#0a7fd0" stroke-width="1.4" fill="none"/></svg></div>
    </div>
  </div>

  <div class="arrow-btn" style="left:550px;top:1550px;border:1.5px solid var(--cyan)"><svg width="16" height="10" viewBox="0 0 16 10"><path d="M15 5H1M5 1L1 5l4 4" stroke="#0e9ee0" stroke-width="1.5" fill="none"/></svg></div>
  <div class="arrow-btn" style="left:614px;top:1550px;background:var(--cyan)"><svg width="16" height="10" viewBox="0 0 16 10"><path d="M1 5h14M11 1l4 4-4 4" stroke="#fff" stroke-width="1.5" fill="none"/></svg></div>
</section>

<section class="testimonial">
  <div class="photo" role="img" aria-label="Capitol building seen across a green lawn with trees" style="left:0;top:1674px;width:522px;height:445px;background:linear-gradient(180deg,#8fb2d6 0%,#c7d6e4 45%,#9aa39a 65%,#6f8c3a 85%,#4d6b26 100%)"></div>
  <div class="abs" style="left:228px;top:1865px;width:62px;height:62px;background:var(--blue-btn);border:3px solid rgba(255,255,255,.6);display:flex;align-items:center;justify-content:center"><svg width="22" height="24" viewBox="0 0 22 24"><path d="M2 1l19 11L2 23z" fill="#fff"/></svg></div>
  <div class="abs" style="left:314px;top:2023px;width:248px;height:73px;background:#fff;border-radius:8px;box-shadow:0 8px 20px rgba(0,0,0,.15)">
    <div class="abs" style="left:22px;top:20px;font-size:13px;font-weight:500;line-height:17px">250+ Global<br>Clients</div>
    <div class="abs" style="left:128px;top:18px;width:38px;height:38px;border-radius:50%;background:linear-gradient(135deg,#e06a9a,#6f6ac8);border:2px solid #fff"></div>
    <div class="abs" style="left:148px;top:18px;width:38px;height:38px;border-radius:50%;background:linear-gradient(135deg,#e9a04c,#b33a3a);border:2px solid #fff"></div>
    <div class="abs" style="left:168px;top:18px;width:38px;height:38px;border-radius:50%;background:linear-gradient(135deg,#c25b5b,#4a2f2f);border:2px solid #fff"></div>
    <div class="abs" style="left:188px;top:18px;width:38px;height:38px;border-radius:50%;background:var(--blue-btn);border:2px solid #fff;color:#fff;display:flex;align-items:center;justify-content:center;font-size:18px">+</div>
  </div>
  <div class="tag light" style="left:606px;top:1694px">Our Testimonials</div>
  <div class="h2" style="left:606px;top:1721px;color:#fff">Hear What Our <em>Clients Say</em></div>
  <svg class="abs" style="left:606px;top:1790px" width="96" height="16" viewBox="0 0 96 16">
    <g fill="#f5b623"><path id="st" d="M8 0l2.4 5 5.4.6-4 3.7 1.1 5.4L8 12 3.1 14.7 4.2 9.3 .2 5.6 5.6 5z"/><use href="#st" x="20"/><use href="#st" x="40"/><use href="#st" x="60"/><use href="#st" x="80"/></g>
  </svg>
  <p class="quote-text">It is a long established fact that a reader will be distracted by the readable content of a page when looking at its layout. The point of using Lorem Ipsum is that it has a more-or-less normal distribution of letters, as opposed to using 'Content here, content here', making it look like readable English.</p>
  <div class="abs" style="left:606px;top:1951px;width:426px;height:1px;background:rgba(255,255,255,.35)"></div>
  <div class="abs" style="left:907px;top:1932px;width:38px;height:38px;border-radius:50%;background:var(--navy);border:1.5px solid var(--cyan);display:flex;align-items:center;justify-content:center;color:var(--cyan);font-size:26px;font-weight:600;line-height:1;padding-top:10px">”</div>
  <div class="photo" role="img" aria-label="Portrait of the client" style="left:606px;top:1983px;width:56px;height:56px;border-radius:50%;background:linear-gradient(135deg,#d9d9d9,#6b6b6b);border:2px solid #fff"></div>
  <div class="abs" style="left:676px;top:1989px;font-size:15px;font-weight:500;color:#fff">Martin K. Ellery</div>
  <div class="abs" style="left:676px;top:2013px;font-size:12px;color:#c7d2df">CEO &amp; Founder</div>
</section>

<section class="team">
  <div class="tag" style="left:563px;top:2205px">Our Team</div>
  <div class="h2" style="left:0;top:2232px;width:1200px;text-align:center">Meet The Our <em>Experts</em></div>
  <div class="member" style="left:174px">
    <div class="photo" role="img" aria-label="Portrait of Clara Wendt" style="background:linear-gradient(180deg,#9cc8ef,#5e9dd9 60%,#1e2a45)"></div>
    <div class="name">Clara Wendt</div><div class="role">Web Designer</div>
    <div class="socials"><span><i></i></span><span><i></i></span></div>
  </div>
  <div class="member" style="left:398px">
    <div class="photo" role="img" aria-label="Portrait of Owen Darrow" style="background:linear-gradient(180deg,#9cc8ef,#5e9dd9 60%,#1c1f2a)"></div>
    <div class="name">Owen Darrow</div><div class="role">Web Designer</div>
    <div class="socials"><span><i></i></span><span><i></i></span></div>
  </div>
  <div class="member" style="left:619px">
    <div class="photo" role="img" aria-label="Portrait of Nadia Pryce" style="background:linear-gradient(180deg,#9cc8ef,#6ea9dd 60%,#a9c7ea)"></div>
    <div class="name">Nadia Pryce</div><div class="role">Web Designer</div>
    <div class="socials"><span><i></i></span><span><i></i></span></div>
  </div>
  <div class="member" style="left:842px">
    <div class="photo" role="img" aria-label="Portrait of Julian Harte" style="background:linear-gradient(180deg,#9cc8ef,#5e9dd9 60%,#1a2436)"></div>
    <div class="name">Julian Harte</div><div class="role">Web Designer</div>
    <div class="socials"><span><i></i></span><span><i></i></span></div>
  </div>
</section>

<section class="cta">
  <div class="photo" role="img" aria-label="Federal building with a flag and autumn tree"></div>
  <div class="abs" style="left:56px;top:40px;font-size:28px;font-weight:500;line-height:44px;color:#fff;white-space:nowrap">We Are Federal IT Consulting<br>We Make Future!</div>
  <p class="abs" style="left:56px;top:150px;font-size:13px;line-height:23px;color:#fff;white-space:nowrap">There are many variations of passages of Lorem Ipsum<br>available, but the majority have suffered alteration in some form.</p>
  <div class="btn" style="left:56px;top:236px;width:144px;height:41px;background:#fff;color:var(--blue);box-shadow:none">Get Started Now</div>
  <svg class="abs" style="left:212px;top:210px" width="110" height="60" viewBox="0 0 110 60"><path d="M2 58c20-4 40-10 60-28" stroke="#fff" stroke-dasharray="4 4" fill="none" opacity=".7"/><path d="M78 14l22-8-10 20-4-8z" fill="none" stroke="#fff" stroke-width="1.3" opacity=".8"/></svg>
</section>

<section class="certs">
  <div class="tag" style="left:542px;top:3146px">Certifications</div>
  <div class="h2" style="left:0;top:3173px;width:1200px;text-align:center">Certificates Of The Most<br>Popular <em>Brands</em></div>
  <div class="arrow-btn" style="left:140px;top:3356px;border:1.5px solid var(--cyan)"><svg width="8" height="12" viewBox="0 0 8 12"><path d="M7 1L2 6l5 5" stroke="#0e9ee0" stroke-width="1.6" fill="none"/></svg></div>
  <div class="cert" role="img" aria-label="Certificate of achievement" style="left:196px;width:253px;background:linear-gradient(135deg,#fbf7f0,#efe4d4)"></div>
  <div class="cert" role="img" aria-label="Certificate of achievement" style="left:481px;width:240px;background:linear-gradient(135deg,#f4f4f2,#dcdfe5)"></div>
  <div class="cert" role="img" aria-label="Certificate of achievement" style="left:752px;width:252px;background:linear-gradient(135deg,#eef0f3,#cfd6e0)"></div>
  <div class="arrow-btn" style="left:1023px;top:3356px;background:var(--blue-btn)"><svg width="8" height="12" viewBox="0 0 8 12"><path d="M1 1l5 5-5 5" stroke="#fff" stroke-width="1.6" fill="none"/></svg></div>
</section>

<footer class="footer">
  <div class="brand" style="left:142px;top:68px;font-size:40px;color:#fff"><span class="dot" style="width:52px;height:52px;border-width:5px"></span>Brisolux</div>
  <div class="fcol" style="left:511px"><h4>Quick Links</h4><a>Home</a><a>About Us</a><a>Services</a></div>
  <div class="fcol" style="left:674px"><h4>Resources</h4><a>Privacy Policy</a><a>Terms Of Service</a></div>
  <div class="fcol" style="left:852px;width:220px"><h4>Contact Info</h4>
    <div class="contact-row"><svg width="14" height="18" viewBox="0 0 14 18"><path d="M7 1a6 6 0 0 0-6 6c0 4.5 6 10 6 10s6-5.5 6-10a6 6 0 0 0-6-6z" fill="none" stroke="#0e9ee0" stroke-width="1.6"/><circle cx="7" cy="7" r="2" fill="#0e9ee0"/></svg><span>418 Lorem Avenue, #210<br>Sample Road 5678</span></div>
    <div class="contact-row"><svg width="16" height="12" viewBox="0 0 16 12"><rect x="1" y="1" width="14" height="10" rx="1" fill="#0e9ee0"/><path d="M1 1l7 5 7-5" stroke="#081b35" stroke-width="1.2" fill="none"/></svg><span>info@brisoluxgrp-example.com</span></div>
    <div class="contact-row"><svg width="14" height="14" viewBox="0 0 14 14"><path d="M3 1l3 3-1.5 2a8 8 0 0 0 3.5 3.5L10 8l3 3-2 2C6 13 1 8 1 3z" fill="#0e9ee0"/></svg><span>555-204-3188</span></div>
  </div>
  <div class="abs" style="left:142px;top:266px;width:916px;height:1px;background:rgba(255,255,255,.18)"></div>
  <div class="abs" style="left:142px;top:294px;font-size:12px">© 2024 Brisolux. All rights reserved.</div>
  <div class="abs" style="left:909px;top:288px;display:flex;gap:12px">
    <span style="width:28px;height:28px;border-radius:50%;background:var(--blue-btn)"></span>
    <span style="width:28px;height:28px;border-radius:50%;background:var(--blue-btn)"></span>
    <span style="width:28px;height:28px;border-radius:50%;background:var(--blue-btn)"></span>
    <span style="width:28px;height:28px;border-radius:50%;background:var(--blue-btn)"></span>
  </div>
</footer>

</body>
</html>
```